Black Car Limousine transportation business in Naples Florida

Always stand for my reliability and RVD stands for Love, K and M are the first initials of my children's names. It should show professionalism and a dedication to customer service. We keep our clients identities private. Show our professionalism. We are Black car Black tie company. We service transportation on a reserve basis to and from residents, airports, casinos, hotels,

Target Market(s)

It is a Private car service. High end clients. Businesses, Celebrity and athletes. Service to airports, hotels, special events.

Industry/Entity Type

Business

Contact Information for Business Card

A pearl metallic or Luster card. Standard business card size. Would like the name, Company email, show we take credit cards and phone number. Currently I don't have a website but will like to add later.

Logo Text

STEADFAST RVD TRANSPORTATION

Font styles to use
Serif

Colors
eaeaea
000000

Requirements
Must have
• Must have Company email, show we take credit cards and phone number. Currently I don't have a website but will like to add later.
Nice to have
• Would like to stay with a black and white theme. Open to some color trim.
Should not have
• Open to suggestions

```html
<!DOCTYPE html>
<html lang="en">
<head>
<meta charset="utf-8">
<title>Steadfast RVD Transportation – Business Card</title>
<link rel="stylesheet" href="https://fonts.googleapis.com/css2?family=Open+Sans:ital,wght@0,400;0,600;0,700;1,700&display=swap">
<style>
  :root {
    --stage: #b4b4b4;
    --paper: #ffffff;
    --ink: #000000;
    --ink-soft: #1a1a1a;
    --grey-text: #4a4a4a;
    --logo-grey: #8c8c8c;
    --ghost: #eaeaea;
    --white: #ffffff;
  }
  * { margin: 0; padding: 0; box-sizing: border-box; }
  html, body {
    width: 1105px; height: 1200px; overflow: hidden;
    background: var(--stage);
    font-family: "Open Sans", Arial, sans-serif;
  }
  .card {
    position: absolute; left: 193px; width: 720px; height: 410px;
    overflow: hidden;
    box-shadow: 0 4px 10px rgba(0,0,0,0.35);
  }
  .card--front { top: 167px; background: var(--paper); }
  .card--back  { top: 623px; background: var(--ink); }

  .brand-tab {
    position: absolute; left: 54px; top: 0; width: 136px; height: 113px;
    background: var(--ink);
  }
  .vehicle-thumb {
    position: absolute; left: 52px; top: 95px; width: 140px; height: 58px;
    border-radius: 14px 22px 8px 8px;
    background: linear-gradient(180deg, #3a3a3a 0%, #0c0c0c 70%, #555 100%);
  }
  .wordmark {
    position: absolute; left: 200px; top: 92px;
    color: var(--logo-grey); font-weight: 700; font-size: 20px;
    line-height: 1.25; letter-spacing: 1px;
  }
  .vehicle-ghost {
    position: absolute; left: 276px; top: 128px; width: 460px; height: 290px;
    border-radius: 90px 40px 0 0;
    background: radial-gradient(ellipse at 55% 45%, #dcdcdc 0%, var(--ghost) 55%, #f6f6f6 100%);
  }
  .holder {
    position: absolute; left: 54px; top: 208px;
  }
  .holder__name {
    font-size: 25px; font-weight: 600; color: var(--ink-soft); letter-spacing: 0.5px;
  }
  .holder__title {
    font-size: 19px; color: var(--grey-text); margin-top: 0;
  }
  .contacts {
    position: absolute; left: 54px; top: 277px; list-style: none;
  }
  .contacts li {
    display: flex; align-items: center; height: 28px;
    font-size: 18px; color: var(--ink-soft);
  }
  .contacts svg { width: 17px; height: 17px; margin-right: 11px; fill: var(--ink); }

  .vehicle-hero {
    position: absolute; left: 166px; top: 130px; width: 388px; height: 158px;
    border-radius: 40px 70px 14px 14px;
    background: linear-gradient(180deg, #2c2c2c 0%, #0a0a0a 60%, #3c3c3c 100%);
  }
  .floor-line {
    position: absolute; left: 83px; top: 288px; width: 560px; height: 2px;
    background: linear-gradient(90deg, transparent, #d8d8d8 50%, transparent);
  }
  .payment-note {
    position: absolute; left: 0; right: 0; top: 334px;
    display: flex; justify-content: center; align-items: center;
    color: var(--white); font-style: italic; font-weight: 700; font-size: 19px;
  }
  .payment-note svg { width: 26px; height: 18px; margin-right: 9px; }
</style>
</head>
<body>
  <section class="card card--front">
    <div class="vehicle-ghost" role="img" aria-label="Faint photo of a black luxury SUV"></div>
    <div class="brand-tab"></div>
    <div class="vehicle-thumb" role="img" aria-label="Photo of a black luxury SUV"></div>
    <div class="wordmark">STEADFAST RVD<br>TRANSPORTATION</div>

    <div class="holder">
      <p class="holder__name">DANIEL REYES</p>
      <p class="holder__title">CEO/Founder</p>
    </div>

    <ul class="contacts">
      <li>
        <svg viewBox="0 0 24 24"><path d="M6.6 10.8a15 15 0 0 0 6.6 6.6l2.2-2.2c.3-.3.7-.4 1-.2 1.1.4 2.3.6 3.6.6.6 0 1 .4 1 1V20c0 .6-.4 1-1 1A17 17 0 0 1 3 4c0-.6.4-1 1-1h3.5c.6 0 1 .4 1 1 0 1.3.2 2.5.6 3.6.1.3 0 .7-.2 1z"/></svg>
        239 555 0184
      </li>
      <li>
        <svg viewBox="0 0 24 24"><path d="M2 5h20v14H2z M3 6l9 7 9-7" fill="none" stroke="#000" stroke-width="0"/><path d="M2 5h20v2l-10 7L2 7z"/><path d="M2 9l10 7 10-7v10H2z"/></svg>
        hello@steadfastrvd.com
      </li>
      <li>
        <svg viewBox="0 0 24 24"><circle cx="12" cy="12" r="10"/><path d="M6 8c2 0 3 1 3 3s2 2 2 4-1 3-1 5M14 4c0 2 2 2 3 4s3 2 4 3" fill="none" stroke="#fff" stroke-width="1.6"/></svg>
        www.steadfastrvd.com
      </li>
    </ul>
  </section>

  <section class="card card--back">
    <div class="vehicle-hero" role="img" aria-label="Photo of a black luxury SUV"></div>
    <div class="floor-line"></div>
    <p class="payment-note">
      <svg viewBox="0 0 26 18"><rect x="1" y="1" width="24" height="16" rx="3" fill="#fff"/><rect x="1" y="5" width="24" height="3" fill="#000"/><rect x="4" y="11" width="8" height="2" fill="#000"/></svg>
      We accept credit cards
    </p>
  </section>
</body>
</html>
```